All Natural Mosquito Repellent

My company, BrightPebble Company has created an all natural mosquito repellent. I already have other all natural products that I have developed and created labels for. I will include a copy of that label so you have something to work from. I will need two labels. One for the front of the bottle and one for the back. The back label will need space for a UPC. The labels need to be 63mm (H) x 39mm (W)

Target Market(s)

Consumers, Organic, People who like natural products

Font styles to use
Other font styles liked:
• A combination of both Serif and Sans Serif

Requirements
Must have
• Use the words Organic, All Natural, Travel size, made in the USA label
Nice to have
• tag line: Don't beat them off. Spray them away.

```html
<!DOCTYPE html>
<html lang="en">
<head>
<meta charset="utf-8">
<title>BrightPebble Company – Pebble Mosquito Repellent Label</title>
<link rel="stylesheet" href="https://fonts.googleapis.com/css2?family=Arvo:wght@700&family=Old+Standard+TT&family=Open+Sans:wght@400;600&family=Oswald:wght@500;600&display=swap">
<style>
  :root {
    --sun-yellow: #fbcc57;
    --leaf-green: #1f9a46;
    --title-teal: #14996f;
    --pill-teal: #1a9a73;
    --ink: #1c1c1c;
    --brand-brown: #4a4543;
    --paper: #ffffff;
    --backdrop: #ffffff;
    --alert-red: #e8201f;
  }
  * { margin: 0; padding: 0; box-sizing: border-box; }
  html, body {
    width: 1200px; height: 1200px; overflow: hidden;
    background: var(--backdrop);
  }
  .front-label {
    position: absolute;
    left: 290px; top: 100px;
    width: 620px; height: 1000px;
    background: var(--paper);
    overflow: hidden;
    box-shadow: 0 6px 18px rgba(0,0,0,0.25);
    font-family: "Open Sans", sans-serif;
    color: var(--ink);
  }
  .header-arc { position: absolute; left: 0; top: 0; width: 620px; height: 320px; }
  .brand {
    position: absolute; left: 0; top: 110px; width: 620px;
    text-align: center;
  }
  .brand-mark {
    display: inline-block; width: 54px; height: 54px; border-radius: 50%;
    background: var(--brand-brown); margin-bottom: 10px;
  }
  .brand-name {
    font-family: "Open Sans", sans-serif; font-weight: 400;
    font-size: 30px; letter-spacing: 0.5px; color: var(--brand-brown);
  }
  .brand-sub {
    display: flex; justify-content: center; gap: 40px;
    font-size: 11px; font-weight: 600; color: var(--brand-brown); margin-top: 2px;
  }
  .product-line {
    position: absolute; left: 0; top: 355px; width: 620px; text-align: center;
    font-family: "Open Sans", sans-serif; font-size: 36px; letter-spacing: -0.5px;
  }
  .product-name {
    position: absolute; left: 0; top: 398px; width: 620px; text-align: center;
    font-family: "Oswald", sans-serif; font-weight: 600; font-size: 54px;
    color: var(--title-teal); letter-spacing: 0.5px; line-height: 1.1;
    transform: scaleX(0.92);
  }
  .tagline {
    position: absolute; left: 0; top: 472px; width: 620px; text-align: center;
    font-family: "Old Standard TT", serif; font-size: 36px; line-height: 42px;
    letter-spacing: 0.5px;
  }
  .claims {
    position: absolute; left: 90px; top: 598px; width: 200px; text-align: center;
  }
  .claim-pill {
    display: block; background: var(--pill-teal); color: var(--paper);
    border-radius: 9px; height: 40px; line-height: 40px;
    font-family: "Oswald", sans-serif; font-weight: 500; font-size: 25px;
    letter-spacing: 0.3px;
  }
  .claim-text { font-size: 28px; line-height: 32px; margin-top: 4px; letter-spacing: -0.5px; }
  .pest-icon {
    position: absolute; left: 340px; top: 575px; width: 190px; height: 190px;
    border-radius: 50%; border: 12px solid var(--alert-red);
    background: radial-gradient(circle, #5a5a5a 0%, #d8d8d8 45%, #ffffff 70%);
  }
  .grass-field {
    position: absolute; left: 0; top: 735px; width: 620px; height: 265px;
    background: linear-gradient(to bottom, rgba(31,154,70,0) 0%, rgba(31,154,70,0.55) 30%, var(--leaf-green) 65%, var(--leaf-green) 100%);
  }
  .origin-badge {
    position: absolute; left: 30px; top: 895px; width: 260px;
    display: flex; align-items: center; gap: 8px; color: var(--paper);
  }
  .origin-rule { flex: 1; height: 3px; background: var(--paper); }
  .origin-text {
    font-family: "Arvo", serif; font-weight: 700; font-size: 34px;
    line-height: 40px; text-align: left;
  }
  .net-weight {
    position: absolute; left: 420px; top: 912px; width: 140px; text-align: center;
    font-family: "Oswald", sans-serif; font-weight: 600; font-size: 23px;
    line-height: 30px; color: var(--paper); letter-spacing: -0.5px;
  }
</style>
</head>
<body>
  <section class="front-label">
    <svg class="header-arc" viewBox="0 0 620 320" aria-hidden="true">
      <path d="M0 0 H620 V185 Q310 420 0 185 Z" fill="var(--leaf-green)"/>
      <path d="M0 0 H620 V185 Q310 400 0 185 Z" fill="var(--sun-yellow)"/>
    </svg>

    <div class="brand">
      <span class="brand-mark"></span>
      <div class="brand-name">BrightPebble Company</div>
      <div class="brand-sub"><span>crafted by hand, with love</span><span>in the U.S.A.</span></div>
    </div>

    <div class="product-line">PEBBLE</div>
    <h1 class="product-name">MOSQUITO REPELLENT</h1>
    <p class="tagline">“Don't beat them off<br>Spray them away”</p>

    <div class="claims">
      <span class="claim-pill">ALL NATURAL</span>
      <p class="claim-text">organic<br>Travel Size</p>
    </div>

    <div class="pest-icon" role="img" aria-label="Mosquito inside a red no-entry sign"></div>

    <div class="grass-field" role="img" aria-label="Green grass blades along the bottom of the label"></div>

    <div class="origin-badge">
      <span class="origin-rule"></span>
      <span class="origin-text">Made in<br>the USA</span>
      <span class="origin-rule"></span>
    </div>

    <p class="net-weight">NET WEIGHT<br>50 ML</p>
  </section>
</body>
</html>
```